Heritage Hollow Business Cards

Require a business card design. <br/><br/>Needs to include logo (either round or long version) plus these details:<br/>Maya Torvell<br/>Heritage Hollow<br/>maya@kelvadtrading.com.au<br/>02 6481 7395<br/>PO Box Glenwarra NSW 2791<br/>www.heritagehollow.com.au<br/><br/>I need in an editable format so that I can create for multiple staff members. <br/><br/>

Target Market(s)

We are an online store selling renovation products to home owners are builders. Looking for a classic classy design.

Industry/Entity Type

Home And Garden

Contact Information for Business Card

Maya Torvell
Heritage Hollow
maya@kelvadtrading.com.au
02 6481 7395
PO Box Glenwarra NSW 2791
www.heritagehollow.com.au

Colors

Designer to choose colors to be used in the design.

Requirements
Must have
• Must include Logo.

```html
<!DOCTYPE html>
<html lang="en">
<head>
<meta charset="utf-8">
<title>Heritage Hollow Business Cards</title>
<link rel="stylesheet" href="https://fonts.googleapis.com/css2?family=Arimo:wght@400;700&display=swap">
<style>
  :root {
    --backdrop: #5b5b5b;
    --card-light: #ffffff;
    --card-dark: #262626;
    --card-dark-edge: #303030;
    --ink: #1a1a1a;
    --ink-soft: #2b2b2b;
    --on-dark: #e8e8e8;
    --shadow: rgba(0, 0, 0, 0.35);
  }
  * { margin: 0; padding: 0; box-sizing: border-box; }
  html, body {
    width: 1200px;
    height: 900px;
    overflow: hidden;
    background: var(--backdrop);
    font-family: "Arimo", Arial, sans-serif;
  }
  .stage { position: relative; width: 1200px; height: 900px; }

  .card {
    position: absolute;
    top: 200px;
    width: 310px;
    height: 503px;
    box-shadow: 3px 4px 6px var(--shadow);
    overflow: hidden;
  }
  .card--front {
    left: 253px;
    background: var(--card-light);
    border-radius: 62px 0 62px 0;
    color: var(--ink);
  }
  .card--back {
    left: 627px;
    border-radius: 0 62px 0 62px;
  }
  .card-texture {
    position: absolute;
    inset: 0;
    background: radial-gradient(ellipse at 55% 45%, var(--card-dark-edge) 0%, var(--card-dark) 70%);
  }

  .brand-mark {
    position: absolute;
    border-radius: 50%;
    display: flex;
    align-items: center;
    justify-content: center;
    text-align: center;
    font-weight: 400;
    line-height: 1.05;
  }
  .card--front .brand-mark {
    left: 75px; top: 71px;
    width: 156px; height: 156px;
    border: 1.5px solid var(--ink);
    color: var(--ink);
    font-size: 23px;
  }
  .card--back .brand-mark {
    left: 75px; top: 176px;
    width: 160px; height: 160px;
    border: 1.5px solid var(--on-dark);
    color: var(--on-dark);
    font-size: 23px;
  }

  .holder-name {
    position: absolute;
    left: 39px; top: 299px;
    font-size: 17px;
    font-weight: 700;
    letter-spacing: 0.3px;
  }
  .contact-list {
    position: absolute;
    left: 39px; top: 335px;
    list-style: none;
    font-size: 14px;
    color: var(--ink-soft);
  }
  .contact-list li {
    display: flex;
    align-items: center;
    gap: 3px;
    height: 19px;
  }
  .contact-list svg { width: 16px; height: 16px; flex: none; }

  .postal {
    position: absolute;
    left: 41px; top: 406px;
    font-size: 14px;
    line-height: 18px;
    color: var(--ink-soft);
    font-style: normal;
  }
  .postal-company { font-weight: 700; color: var(--ink); }
</style>
</head>
<body>
<main class="stage">

  <section class="card card--front" aria-label="Business card front">
    <div class="brand-mark">Heritage<br>Hollow</div>

    <h1 class="holder-name">MAYA TORVELL</h1>

    <ul class="contact-list">
      <li>
        <svg viewBox="0 0 16 16" aria-hidden="true">
          <rect x="1" y="1" width="14" height="14" rx="2.5" fill="none" stroke="#1a1a1a" stroke-width="1.4"/>
          <path d="M5 4.2c.6-.5 1.2-.3 1.5.3l.6 1.2c.2.5 0 .9-.4 1.2l-.4.3c.4 1 1.2 1.8 2.1 2.2l.3-.4c.3-.4.8-.5 1.2-.3l1.2.6c.6.3.7.9.3 1.5-.6.8-1.5 1-2.4.6C7.3 10.6 5.5 8.7 4.7 6.7c-.3-.9-.2-1.8.3-2.5z" fill="#1a1a1a"/>
        </svg>
        <span>02 6481 7395</span>
      </li>
      <li>
        <svg viewBox="0 0 16 16" aria-hidden="true">
          <rect x="1" y="3.5" width="14" height="9" fill="#1a1a1a"/>
          <path d="M1 3.5l7 5 7-5" fill="none" stroke="#fff" stroke-width="1.2"/>
        </svg>
        <span>maya@kelvadtrading.com.au</span>
      </li>
      <li>
        <svg viewBox="0 0 16 16" aria-hidden="true">
          <g fill="none" stroke="#1a1a1a" stroke-width="1.3">
            <circle cx="8" cy="8" r="6.6"/>
            <ellipse cx="8" cy="8" rx="3" ry="6.6"/>
            <path d="M1.4 8h13.2M2.5 4.8h11M2.5 11.2h11"/>
          </g>
        </svg>
        <span>www.heritagehollow.com.au</span>
      </li>
    </ul>

    <address class="postal">
      <span class="postal-company">HERITAGE HOLLOW</span><br>
      PO Box Glenwarra<br>
      NSW 2791
    </address>
  </section>

  <section class="card card--back" aria-label="Business card back">
    <div class="card-texture" role="img" aria-label="Faint hand-drawn crossing line texture on charcoal"></div>
    <div class="brand-mark">Heritage<br>Hollow</div>
  </section>

</main>
</body>
</html>
```